Computer consultant business card

Bexil Software is a newly started computer consulting company. It's a small one-man company that provides mostly Vornix applications but also websites in collaboration with designers. I'm running this company on the side of full time university studies.

I want the final design to be clean and memorable. Be creative! :)

Some inspiration:
http://www.pixelmarta.com/design/48317
http://www.pixelmarta.com/design/2739164/business-card-design-by-frostlynk
http://www.pixelmarta.com/design/604281/business-card-design-by-koralind-vestrabanu

See attachment for my company logo.
Updates

I would like to thank everyone for submitting! I'll need a couple of days to review and ultimately select a design.

Target Market(s)

Non-technical entrepreneurs and small companies.

Industry/Entity Type

University

Requirements
Must have
• My company logo.
In any way, both colors from my logo.
First- and last name, e-mail and phone number.
Double-sided design.
Nice to have
• Something creative with the symbol in my logo

```html
<!DOCTYPE html>
<html lang="en">
<head>
<meta charset="utf-8">
<title>Bexil Software — Business Card</title>
<link rel="stylesheet" href="https://fonts.googleapis.com/css2?family=Arimo:wght@400;700&family=Orbitron:wght@700&display=swap">
<style>
  :root {
    --backdrop: #e4e4e2;
    --paper: #ffffff;
    --band: #2f2926;
    --accent: #1b9ad6;
    --ink: #3a3a3a;
    --ink-soft: #4a4a4a;
  }
  * { margin: 0; padding: 0; box-sizing: border-box; }
  html, body {
    width: 1200px;
    height: 900px;
    overflow: hidden;
    background: var(--backdrop);
  }
  .canvas {
    position: relative;
    width: 1200px;
    height: 900px;
  }
  .card {
    position: absolute;
    left: 250px;
    width: 700px;
    height: 400px;
    background: var(--paper);
    box-shadow: 0 6px 18px rgba(0,0,0,0.18);
    overflow: hidden;
  }
  .card--front { top: 40px; }
  .card--back { top: 470px; }
  .card__art {
    position: absolute;
    inset: 0;
    width: 700px;
    height: 400px;
  }
  .wordmark {
    position: absolute;
    display: flex;
    align-items: center;
    font-family: "Arimo", Arial, sans-serif;
    font-weight: 700;
    color: var(--ink);
    letter-spacing: 1px;
    white-space: nowrap;
  }
  .wordmark__dot {
    flex: none;
    border-radius: 50%;
    background: var(--accent);
  }
  .card--front .wordmark {
    left: 50px;
    top: 78px;
    font-size: 46px;
    gap: 16px;
  }
  .card--front .wordmark__dot { width: 46px; height: 46px; }
  .card--back .wordmark {
    left: 70px;
    top: 150px;
    font-size: 64px;
    gap: 22px;
  }
  .card--back .wordmark__dot { width: 90px; height: 90px; }
  .identity {
    position: absolute;
    right: 40px;
    top: 34px;
    text-align: right;
    font-family: "Orbitron", "Arial Black", sans-serif;
    font-weight: 700;
    color: var(--accent);
    line-height: 1;
    white-space: nowrap;
  }
  .identity__name { font-size: 26px; letter-spacing: 1px; }
  .identity__role { font-size: 14px; letter-spacing: 1.5px; margin-top: 4px; }
  .contact {
    position: absolute;
    left: 52px;
    top: 196px;
    list-style: none;
    font-family: "Arimo", Arial, sans-serif;
    font-size: 15px;
    color: var(--ink-soft);
  }
  .contact__item {
    display: flex;
    align-items: center;
    gap: 12px;
    height: 24px;
    white-space: nowrap;
  }
  .contact__icon { width: 14px; height: 14px; flex: none; }
</style>
</head>
<body>
<main class="canvas">

  <section class="card card--front" aria-label="Business card front">
    <svg class="card__art" viewBox="0 0 700 400" aria-hidden="true">
      <path d="M0,322 Q430,300 700,108 L700,400 L0,400 Z" fill="var(--band)"/>
      <path d="M0,307 Q425,284 700,92" fill="none" stroke="var(--accent)" stroke-width="5"/>
    </svg>
    <div class="wordmark"><span class="wordmark__dot"></span><span>Bexil</span></div>
    <div class="identity">
      <div class="identity__name">LUKASVEEN</div>
      <div class="identity__role">GRAPHIC DESIGNER</div>
    </div>
    <ul class="contact">
      <li class="contact__item">
        <svg class="contact__icon" viewBox="0 0 14 14"><path d="M4 1 L6 4 L4.5 5.5 Q5.5 8.5 8.5 9.5 L10 8 L13 10 L11.5 13 Q3 12 1 2.5 Z" fill="var(--accent)"/></svg>
        <span>+(000) 4821 9370</span>
      </li>
      <li class="contact__item">
        <svg class="contact__icon" viewBox="0 0 14 14"><rect x="1" y="3" width="12" height="8" fill="none" stroke="var(--accent)" stroke-width="1.4"/><path d="M1 3 L7 8 L13 3" fill="none" stroke="var(--accent)" stroke-width="1.4"/></svg>
        <span>lukas@bexilsoft.com</span>
      </li>
      <li class="contact__item">
        <svg class="contact__icon" viewBox="0 0 14 14"><circle cx="7" cy="7" r="6" fill="var(--accent)"/><path d="M1 7 H13 M7 1 Q3 7 7 13 M7 1 Q11 7 7 13" fill="none" stroke="var(--paper)" stroke-width="1"/></svg>
        <span>www.bexilsoft.com</span>
      </li>
    </ul>
  </section>

  <section class="card card--back" aria-label="Business card back">
    <svg class="card__art" viewBox="0 0 700 400" aria-hidden="true">
      <path d="M700,40 Q640,300 400,400 L700,400 Z" fill="var(--band)"/>
      <path d="M684,30 Q622,290 380,400" fill="none" stroke="var(--accent)" stroke-width="5"/>
    </svg>
    <div class="wordmark"><span class="wordmark__dot"></span><span>Bexil</span></div>
  </section>

</main>
</body>
</html>
```